Design a web site for my business - Brightline Coatings Co.

We are a family business that handles design, fabrication and installation of powder coated aluminum, stainless steel and glass products. Including handrails, privacy slat screens, electric gates and pool fencing. We are based in the Whitsundays in North Queensland and service an area from Airlie Beach to Townsville.

Target Market(s)

Domestic and commercial

Industry/Entity Type

fabrication - manufacturing

Coding

Coded - Design and coding required

Number of Pages Required

5+ page

Colors
0054AA
0677BA
7BADD7
CADEEF
E8F1F8

Requirements
Must have
• photo galleries, contact page, one page for privacy screens, balustrades, glass fencing, stainless steel handrail, powder coated aluminium handrails and pool fencing

```html
<!DOCTYPE html>
<html lang="en">
<head>
<meta charset="utf-8">
<title>Brightline Coatings Co — Precision Fabrication</title>
<link href="https://fonts.googleapis.com/css2?family=Plus+Jakarta+Sans:wght@400;500;600;700;800&display=swap" rel="stylesheet">
<style>
:root{
  --blue:#0054AA;
  --blue-mid:#0677BA;
  --blue-soft:#7BADD7;
  --blue-pale:#CADEEF;
  --blue-wash:#E8F1F8;
  --page:#F3F7FC;
  --ink:#0F1B2D;
  --text:#4A5565;
  --muted:#7A8594;
  --navy:#062A5E;
  --white:#FFFFFF;
}
*{box-sizing:border-box;margin:0;padding:0}
html,body{width:1200px;height:4986px;overflow:hidden}
body{font-family:"Plus Jakarta Sans",sans-serif;background:var(--page);color:var(--ink);position:relative}
.abs{position:absolute}
a{text-decoration:none;color:inherit}

/* nav */
.site-header{position:absolute;left:0;top:0;width:1200px;height:84px;background:var(--white);border-bottom:1px solid #e4e9f0}
.brand{position:absolute;left:66px;top:28px;display:flex;align-items:center;gap:8px;font-size:12px;font-weight:700;color:var(--ink)}
.brand-dot{width:14px;height:14px;border-radius:50%;background:var(--blue)}
.main-nav{position:absolute;right:56px;top:0;height:84px;display:flex;gap:38px;align-items:center;font-size:13px;color:var(--text)}
.main-nav .active{color:var(--ink);font-weight:700;height:84px;display:flex;align-items:center;border-bottom:2px solid var(--ink)}

/* hero */
.hero{position:absolute;left:0;top:84px;width:1200px;height:516px;background:linear-gradient(135deg,#4d5560 0%,#5e5a52 35%,#3b4a3a 70%,#2a3a2c 100%)}
.hero-shade{position:absolute;inset:0;background:linear-gradient(90deg,rgba(10,20,35,.55),rgba(10,20,35,.1))}
.hero h1{position:absolute;left:67px;top:136px;font-size:63px;line-height:76px;font-weight:800;color:var(--white);letter-spacing:-.5px}
.hero p{position:absolute;left:67px;top:302px;width:720px;font-size:17px;line-height:26px;color:var(--white)}
.btn{display:inline-flex;align-items:center;justify-content:center;border-radius:30px;font-weight:700;font-size:17px}
.btn-primary{background:var(--blue);color:var(--white)}
.btn-ghost{color:var(--white)}
.btn-outline{background:var(--blue-wash);color:var(--blue);border:1px solid var(--blue-pale)}

/* eyebrow */
.eyebrow{display:flex;align-items:center;gap:14px;font-size:13px;font-weight:700;color:var(--blue)}
.eyebrow::before{content:"";width:50px;height:1px;background:var(--blue)}
.section-title{font-size:37px;line-height:46px;font-weight:700;color:var(--ink);text-transform:uppercase}

/* about */
.about-band{position:absolute;left:0;top:600px;width:1200px;height:525px;background:var(--blue-wash)}
.about-copy{position:absolute;left:67px;top:668px;width:490px;font-size:17px;line-height:25px;color:var(--ink)}
.about-copy p+p{margin-top:25px}
.photo{background:linear-gradient(135deg,#5d7a55,#2f4a32 60%,#8a7a5e)}
.badge-row{position:absolute;left:24px;bottom:24px;display:flex;gap:28px}
.badge{width:228px;height:56px;background:rgba(120,120,120,.55);border-left:3px solid var(--blue);padding:10px 14px;color:var(--white)}
.badge b{display:block;font-size:14px;font-weight:600}
.badge span{font-size:10px;opacity:.85}
.stat-card{position:absolute;left:925px;top:1078px;width:192px;height:104px;background:var(--white);padding:20px 18px}
.stat-card b{display:block;font-size:34px;font-weight:600;color:var(--blue)}
.stat-card span{font-size:10px;color:var(--ink)}

/* services */
.centered{position:absolute;left:0;width:1200px;text-align:center}
.eyebrow.center{justify-content:center}
.eyebrow.center::before{width:70px}
.service-card{position:absolute;width:341px;background:var(--white);box-shadow:0 4px 16px rgba(0,40,90,.07);padding:18px 18px 28px}
.service-num{position:absolute;left:25px;top:-14px;width:36px;height:36px;background:var(--blue);color:var(--white);font-size:15px;font-weight:600;display:flex;align-items:center;justify-content:center}
.service-img{width:100%;background:linear-gradient(160deg,#c9ced3,#8b969f)}
.service-card h3{font-size:19px;line-height:25px;font-weight:700;margin-top:30px;text-transform:uppercase}
.service-card p{font-size:14px;line-height:21px;color:var(--text);margin-top:12px;width:270px}
.service-card a{display:block;margin-top:12px;font-size:14px;font-weight:700;color:var(--blue)}

/* why */
.why-band{position:absolute;left:0;top:2665px;width:1200px;height:740px;background:var(--blue-wash)}
.feature{position:absolute;left:67px;width:500px;display:flex;gap:32px}
.feature svg{flex:none}
.feature h4{font-size:22px;font-weight:600;margin-bottom:10px}
.feature p{font-size:17px;line-height:24px;color:var(--text)}

/* testimonials */
.quote-card{position:absolute;top:3715px;width:704px;height:315px;background:var(--white);border-radius:22px;box-shadow:0 4px 18px rgba(0,40,90,.07);overflow:hidden}
.stars{position:absolute;left:36px;top:30px;color:var(--blue);font-size:22px;letter-spacing:4px}
.quote-card blockquote{position:absolute;left:36px;top:96px;width:300px;font-size:16px;line-height:27px;color:var(--muted)}
.quote-card .who{position:absolute;left:36px;top:240px;font-size:16px;font-weight:600}
.quote-card .who small{display:block;font-size:12px;font-weight:400;color:var(--text);margin-top:4px}
.quote-img{position:absolute;left:372px;top:22px;width:310px;height:272px;border-radius:8px;background:linear-gradient(180deg,#b3895c,#6d6e70 55%,#3e4247)}

/* footer */
.site-footer{position:absolute;left:27px;top:4595px;width:1146px;height:365px;background:var(--navy);border-radius:28px;color:var(--white)}
.footer-brand{position:absolute;left:66px;top:60px;display:flex;align-items:center;gap:8px;font-size:13px;font-weight:700}
.footer-about{position:absolute;left:66px;top:150px;width:290px;font-size:16px;line-height:27px;color:var(--blue-pale)}
.footer-col{position:absolute;top:58px}
.footer-col h5{font-size:17px;font-weight:700;margin-bottom:18px}
.footer-col li{list-style:none;font-size:14px;line-height:29px;color:var(--blue-pale)}
.footer-rule{position:absolute;left:66px;right:66px;top:320px;border-top:1px solid rgba(202,222,239,.25)}
.footer-legal{position:absolute;left:0;width:100%;top:330px;text-align:center;font-size:14px;color:var(--blue-pale)}
</style>
</head>
<body>

<header class="site-header">
  <div class="brand"><span class="brand-dot"></span>Brightline Coatings Co</div>
  <nav class="main-nav">
    <a class="active">Home</a><a>About Us</a><a>Our Services</a><a>Gallery</a><a>Contact Us</a>
  </nav>
</header>

<section class="hero" role="img" aria-label="Timber home with stainless steel and glass balustrade decks among tropical gardens">
  <div class="hero-shade"></div>
  <h1>PRECISION FABRICATION<br>BUILT TO LAST</h1>
  <p>Custom aluminium and stainless steel handrails, glass balustrades and gates — designed, fabricated and installed by a family-owned Whitsundays team.</p>
  <a class="btn btn-primary abs" style="left:67px;top:394px;width:226px;height:54px">Request Free Quote</a>
  <a class="btn btn-ghost abs" style="left:300px;top:394px;width:184px;height:54px">View Projects</a>
</section>

<div class="about-band"></div>
<div class="about-copy">
  <p>Brightline Coatings Co is a family-owned fabrication studio built on a simple belief: coastal homes and commercial builds deserve hardware that's engineered as carefully as it looks.</p>
  <p>Every handrail, balustrade and gate is measured, fabricated and finished in-house — no shortcuts, no generic stock parts.</p>
</div>
<div class="eyebrow abs" style="right:67px;top:668px">Who We Are</div>
<h2 class="section-title abs" style="right:67px;top:696px;text-align:right;font-size:36px">Crafted with precision<br>installed with pride</h2>
<div class="photo abs" style="left:67px;top:940px;width:525px;height:250px" role="img" aria-label="Timber boardwalk with stainless steel handrail through bushland">
  <div class="badge-row">
    <div class="badge"><b>Family Owned</b><span>Three generations of fabrication craft.</span></div>
    <div class="badge"><b>Built for Coast</b><span>Marine-grade finishes, salt resistant.</span></div>
  </div>
</div>
<div class="abs" style="left:608px;top:828px;width:525px;height:362px;background:linear-gradient(180deg,#8fb0d6 0%,#9fb9cf 30%,#5d7f5a 55%,#a8743f 80%,#5b6670 100%)" role="img" aria-label="Waterfront boardwalk with powder coated railing beside the bay"></div>
<div class="stat-card"><b>14+</b><span>Years serving the Whitsundays</span></div>

<div class="centered" style="top:1308px">
  <div class="eyebrow center">Capabilities</div>
  <h2 class="section-title" style="margin-top:12px">Fabrication built<br>around your project</h2>
  <p style="margin-top:22px;font-size:17px;line-height:25px;color:var(--ink)">Seven core services, one team — from first sketch to finished install,<br>across residential and commercial builds.</p>
</div>

<article class="service-card" style="left:67px;top:1570px;height:437px"><span class="service-num">1</span>
  <div class="service-img" style="height:202px" role="img" aria-label="Frameless glass balustrade on a mezzanine"></div>
  <h3>Glass Balustrades</h3><p>Frameless and semi-frameless glass, engineered for uninterrupted ocean views.</p><a>Request a Quote →</a></article>
<article class="service-card" style="left:428px;top:1570px;height:470px"><span class="service-num">2</span>
  <div class="service-img" style="height:250px;background:linear-gradient(180deg,#4f7a3f,#2f4d2e 50%,#56a6c8 75%,#8a8f94)" role="img" aria-label="Black aluminium pool fence around a garden pool"></div>
  <h3>Pool Fencing</h3><p>Australian Standard compliant fencing built for coastal and commercial pools.</p><a>Request a Quote →</a></article>
<article class="service-card" style="left:790px;top:1570px;height:437px"><span class="service-num">3</span>
  <div class="service-img" style="height:202px;background:linear-gradient(160deg,#e5e5e3,#a8a7a2)" role="img" aria-label="Stainless steel handrail on a concrete staircase"></div>
  <h3>Stainless Steel Handrails</h3><p>Marine-grade 316 stainless, polished or brushed, for balconies and stairs.</p><a>Request a Quote →</a></article>

<article class="service-card" style="left:67px;top:2043px;height:437px"><span class="service-num">4</span>
  <div class="service-img" style="height:218px;background:linear-gradient(180deg,#3c4f3a,#4fb4d4 50%,#8d8e8c)" role="img" aria-label="Glass pool fence beside a timber pool deck"></div>
  <h3>Glass Pool Fencing</h3><p>Compliant, low-profile fencing that keeps pools safe without blocking the view.</p><a>Request a Quote →</a></article>
<article class="service-card" style="left:428px;top:2076px;height:470px"><span class="service-num">5</span>
  <div class="service-img" style="height:250px;background:linear-gradient(160deg,#6c8b57,#3a3f44 55%,#d9d4c8)" role="img" aria-label="Aluminium slat electric gate opening to a courtyard"></div>
  <h3>Electric Gates</h3><p>Automated aluminium and steel gates for driveways and entries.</p><a>Request a Quote →</a></article>
<article class="service-card" style="left:790px;top:2043px;height:437px"><span class="service-num">6</span>
  <div class="service-img" style="height:218px;background:linear-gradient(180deg,#7a8490,#3d4550 55%,#8b8a82)" role="img" aria-label="Black powder coated aluminium handrail on house entry steps"></div>
  <h3>Powder Coated Aluminium Handrails</h3><p>Colour-matched aluminium in any finish, engineered for coastal durability.</p><a>Request a Quote →</a></article>

<div class="why-band"></div>
<div class="eyebrow abs" style="left:67px;top:2734px">Why Brightline</div>
<h2 class="section-title abs" style="left:67px;top:2764px">Engineered for<br>coastal conditions</h2>
<p class="abs" style="right:67px;top:2778px;width:360px;text-align:right;font-size:17px;line-height:25px">Salt air, cyclonic winds and full sun don't get a vote — everything we build is finished to last through it.</p>

<div class="feature" style="top:2928px">
  <svg width="74" height="74" viewBox="0 0 74 74" fill="none" stroke="var(--blue)" stroke-width="3" stroke-linejoin="round"><path d="M8 30l29-12 29 12-29 12z"/><path d="M8 42l29 12 29-12"/><path d="M8 52l29 12 29-12"/><path d="M24 16V6M37 12V2M50 16V6M20 10l4-4 4 4M33 6l4-4 4 4M46 10l4-4 4 4"/></svg>
  <div><h4>Custom Fabrication</h4><p>Every job measured and cut to fit — nothing off the shelf.</p></div>
</div>
<div class="feature" style="top:3084px">
  <svg width="74" height="74" viewBox="0 0 74 74" fill="none" stroke="var(--blue)" stroke-width="3" stroke-linejoin="round"><path d="M10 20l24-12h30L40 20z"/><path d="M10 20h30v10H30v24h10v10H10V54h10V30H10z"/><path d="M40 20l24-12v10l-24 12M40 64l24-12V42"/></svg>
  <div><h4>Premium Materials</h4><p>Marine-grade stainless and architectural aluminium, always.</p></div>
</div>
<div class="feature" style="top:3240px">
  <svg width="74" height="74" viewBox="0 0 74 74" fill="none" stroke="var(--blue)" stroke-width="3" stroke-linejoin="round" stroke-linecap="round"><circle cx="24" cy="26" r="8"/><circle cx="50" cy="26" r="8"/><path d="M8 60c0-10 7-18 16-18s16 8 16 18M34 60c0-10 7-18 16-18s16 8 16 18"/><path d="M37 4v8M22 8l3 6M52 8l-3 6"/></svg>
  <div><h4>Experienced Team</h4><p>Fabricators and installers who know North Queensland conditions.</p></div>
</div>
<div class="abs" style="left:608px;top:2922px;width:525px;height:418px;background:linear-gradient(135deg,#2f3e2c,#5a6e4a 45%,#9aa7a4 75%,#7e8a88);border-right:6px solid var(--blue-pale);border-bottom:6px solid var(--blue-pale)" role="img" aria-label="Frameless glass pool fence panels beside tropical planting"></div>

<div class="centered" style="top:3525px">
  <div class="eyebrow center">Client Feedback</div>
  <h2 class="section-title" style="margin-top:12px">Trusted across the<br>Whitsundays</h2>
</div>

<div class="quote-card" style="left:67px">
  <div class="stars">★★★★★</div>
  <blockquote>We use them on every coastal build now. Measurements are always spot-on and the crew works cleanly around other trades.</blockquote>
  <div class="who">Megan L.<small>Builder, Whitsundays</small></div>
  <div class="quote-img" role="img" aria-label="Grey entry stairs with black aluminium handrails and timber cladding"></div>
</div>
<div class="quote-card" style="left:790px">
  <div class="stars">★★★★★</div>
  <blockquote>The colour-matched aluminium hand rails they fabricated for our development look architectural, not off-the-shelf. Exactly what we specified.</blockquote>
  <div class="who">Paul R.<small>Property Developer, Bowen</small></div>
  <div class="quote-img" role="img" aria-label="Completed development entry with aluminium railings"></div>
</div>

<div class="centered" style="top:4152px">
  <div class="eyebrow center">Get In Touch</div>
  <h2 class="section-title" style="margin-top:14px">Get in touch<br>let's build something<br>exceptional</h2>
  <p style="margin-top:18px;font-size:17px;line-height:25px">Tell us about your project and we'll get back to you with<br>a free, no-obligation quote.</p>
</div>
<a class="btn btn-primary abs" style="left:394px;top:4420px;width:226px;height:56px">Request Free Quote</a>
<a class="btn btn-outline abs" style="left:634px;top:4420px;width:170px;height:56px">View Projects</a>

<footer class="site-footer">
  <div class="footer-brand"><span class="brand-dot" style="background:var(--blue-soft)"></span>Brightline Coatings Co</div>
  <p class="footer-about">Family-owned fabrication of aluminium and stainless steel handrails, glass.</p>
  <div class="footer-col" style="left:430px"><h5>SERVICES</h5><ul><li>Glass Balustrades</li><li>Pool Fencing</li><li>Handrails</li><li>Electric Gates</li><li>Slat Screens</li></ul></div>
  <div class="footer-col" style="left:624px"><h5>COMPANY</h5><ul><li>About Us</li><li>Our Projects</li><li>Request a Quote</li><li>Service Areas</li></ul></div>
  <div class="footer-col" style="left:818px"><h5>CONTACT</h5><ul><li>0700 000 000</li><li>info@brightlinecoatings.com.au</li><li>Mon–Fri: 7am – 4pm</li><li>Sat: By appointment</li></ul></div>
  <div class="footer-rule"></div>
  <p class="footer-legal">© 2026 Brightline Coatings Co. All rights reserved</p>
</footer>

</body>
</html>
```